Business Card Design with existing logo

BrightWren provides inspirational leadership training and coaching for corporate executives. We focus on being challenging, humorous and compassionate, providing the right mix of support and push for individuals and teams to improve their knowledge and performance. The colour purple is essential to the design. We already have a logo we are very happy with - we are curious to see what can be done to come across in a professional, high standard way that sets us apart. Ideally the design should include the photo of Liesel-Joy
Target Market(s)
HR/ Senior Management 500 - 1500 employees
Industry/Entity Type
Leadership
Contact Information for Business Card
BrightWren Coaching Ltd
Inspirational leadership
Liesel-Joy Korhonen Bramwick
Leadership coach and trainer
Telephone: +44 1632 960 418
Mobile: +44 7700 900 562
e-mail: lieseljoy@brightwrencoaching.example
www.brightwrencoaching.example
Requirements
Must have
- The existing logo
Picture of Liesel-Joy

```html
<!DOCTYPE html>
<html lang="en">
<head>
<meta charset="utf-8">
<title>BrightWren Coaching – Business Card</title>
<link rel="stylesheet" href="https://fonts.googleapis.com/css2?family=Open+Sans:wght@300;400;600&display=swap">
<style>
  :root {
    --purple: #6b3d98;
    --charcoal: #4a4a4d;
    --ink: #1d1d1f;
    --paper: #ffffff;
    --backdrop: #c4c4c4;
    --backdrop-light: #dedede;
  }
  * { margin: 0; padding: 0; box-sizing: border-box; }
  html, body { width: 1200px; height: 985px; overflow: hidden; }
  body {
    background: linear-gradient(160deg, var(--backdrop) 0%, var(--backdrop-light) 100%);
    font-family: "Open Sans", Arial, sans-serif;
    position: relative;
  }
  .card {
    position: absolute;
    left: 300px;
    width: 600px;
    height: 343px;
    border-radius: 20px;
    overflow: hidden;
    box-shadow: 0 6px 18px rgba(0,0,0,0.18);
  }

  /* Back of card */
  .card-back { top: 100px; background: var(--charcoal); }
  .card-back .mark-circle {
    position: absolute; left: 40px; top: -85px;
    width: 300px; height: 300px; border-radius: 50%;
    background: var(--purple);
  }
  .card-back .wordmark {
    position: absolute; left: 170px; top: 228px;
    font-size: 30px; font-weight: 400; letter-spacing: 1px;
    color: var(--paper); text-transform: uppercase; line-height: 1;
    white-space: nowrap;
  }
  .card-back .tagline {
    position: absolute; left: 240px; top: 268px;
    font-size: 9px; letter-spacing: 4px; color: var(--paper);
    text-transform: uppercase; font-weight: 300; white-space: nowrap;
  }

  /* Front of card */
  .card-front { top: 540px; background: var(--paper); }
  .side-band {
    position: absolute; left: 0; top: 0; bottom: 0; width: 62px;
    background: var(--purple);
  }
  .rule-dark { position: absolute; left: 66px; top: 0; bottom: 0; width: 4px; background: var(--charcoal); }
  .rule-purple { position: absolute; left: 74px; top: 0; bottom: 0; width: 2px; background: var(--purple); }
  .band-icons {
    position: absolute; left: 20px; bottom: 40px;
    display: flex; flex-direction: column; gap: 12px;
  }
  .band-icons svg { width: 20px; height: 20px; display: block; }

  .logo {
    position: absolute; left: 96px; top: 26px;
    display: flex; align-items: center; gap: 12px;
    white-space: nowrap;
  }
  .logo .mark-dot {
    width: 34px; height: 34px; border-radius: 50%;
    border: 3px solid var(--purple);
  }
  .logo .wordmark {
    font-size: 26px; font-weight: 400; color: var(--purple);
    text-transform: uppercase; letter-spacing: 1px; line-height: 1;
  }
  .logo-tagline {
    position: absolute; left: 144px; top: 64px;
    font-size: 8px; letter-spacing: 4px; color: var(--purple);
    text-transform: uppercase; white-space: nowrap;
  }

  .details { position: absolute; left: 96px; top: 96px; right: 30px; color: var(--ink); }
  .person-name { font-size: 22px; font-weight: 400; line-height: 1.2; white-space: nowrap; }
  .person-role {
    display: flex; align-items: center; gap: 6px;
    font-size: 15px; color: var(--purple); line-height: 1.3; white-space: nowrap;
  }
  .person-role::after { content: ""; flex: 1; height: 1px; background: var(--purple); margin-top: 4px; }
  .company, .contact { font-size: 15px; line-height: 1.35; white-space: nowrap; }
  .contact-block { margin-top: 14px; }
  .web-domain { color: var(--purple); }
</style>
</head>
<body>

<section class="card card-back" aria-label="Back of business card">
  <span class="mark-circle"></span>
  <div class="wordmark">BrightWren Coaching</div>
  <div class="tagline">Inspirational Leadership</div>
</section>

<section class="card card-front" aria-label="Front of business card">
  <div class="side-band"></div>
  <div class="rule-dark"></div>
  <div class="rule-purple"></div>
  <div class="band-icons">
    <svg viewBox="0 0 20 20" aria-label="Phone"><path d="M5 2l3 3-2 2c1 2 3 4 5 5l2-2 3 3-2 3C8 17 3 12 2 5z" fill="none" stroke="#fff" stroke-width="1.4"/></svg>
    <svg viewBox="0 0 20 20" aria-label="Email"><circle cx="10" cy="10" r="3" fill="none" stroke="#fff" stroke-width="1.4"/><path d="M13 8v3c0 2 3 2 3-1a6 6 0 1 0-3 5" fill="none" stroke="#fff" stroke-width="1.4"/></svg>
    <svg viewBox="0 0 20 20" aria-label="Website"><circle cx="10" cy="10" r="7" fill="none" stroke="#fff" stroke-width="1.4"/><ellipse cx="10" cy="10" rx="3" ry="7" fill="none" stroke="#fff" stroke-width="1.2"/><path d="M3 10h14" stroke="#fff" stroke-width="1.2"/></svg>
  </div>

  <div class="logo">
    <span class="mark-dot"></span>
    <span class="wordmark">BrightWren Coaching</span>
  </div>
  <div class="logo-tagline">Inspirational Leadership</div>

  <div class="details">
    <div class="person-name">Liesel-Joy Korhonen Bramwick</div>
    <div class="person-role">Leadership coach and trainer</div>
    <div class="company">BrightWren Coaching Ltd</div>
    <div class="company">Inspirational leadership</div>
    <div class="contact-block">
      <div class="contact">+44 1632 960 418</div>
      <div class="contact">+44 7700 900 562 (Mobile)</div>
      <div class="contact">lieseljoy@brightwrencoaching.example</div>
      <div class="contact">www.<span class="web-domain">brightwrencoaching</span>.example</div>
    </div>
  </div>
</section>

</body>
</html>
```